HearthMile business card and stationary design

We are looking for a simple yet elegant design for our mortgage company business card and stationary.

The card should include:
Name (Marcus Pell)
Title (CEO)
Phone Number (732-555-0182)
Address (48 Birchwell Court, Suite 314, Brookvale, NJ 08421)
Email (email@hearthmile.example)
"NMLS" i.e. (NMLS 61947)
"Company NMLS" (Company NMLS 274615)

Contact Information for Business Card

See above

```html
<!DOCTYPE html>
<html lang="en">
<head>
<meta charset="utf-8">
<title>HearthMile Business Card</title>
<link href="https://fonts.googleapis.com/css2?family=Montserrat:wght@400;500;700&display=swap" rel="stylesheet">
<style>
  :root {
    --page-bg: #c4c4c4;
    --card-bg: #2a2a2a;
    --brand-blue: #0aa3e6;
    --text-white: #ffffff;
    --card-radius: 16px;
  }
  * { margin: 0; padding: 0; box-sizing: border-box; }
  html, body {
    width: 1200px;
    height: 800px;
    overflow: hidden;
  }
  body {
    background: var(--page-bg);
    font-family: "Montserrat", Arial, sans-serif;
    display: flex;
    align-items: center;
    justify-content: center;
    gap: 50px;
  }
  .card {
    position: relative;
    width: 540px;
    height: 310px;
    background: var(--card-bg);
    border-radius: var(--card-radius);
    border-bottom: 2px solid var(--brand-blue);
    box-shadow: 0 14px 30px rgba(0, 0, 0, 0.35);
    color: var(--text-white);
    overflow: hidden;
  }

  /* Front */
  .card-front .brand-name {
    position: absolute;
    top: 40px;
    right: 36px;
    font-size: 52px;
    font-weight: 500;
    letter-spacing: 1px;
    color: var(--brand-blue);
    white-space: nowrap;
  }
  .card-front .divider {
    position: absolute;
    top: 138px;
    left: 36px;
    right: 36px;
    height: 1px;
    background: var(--brand-blue);
  }
  .person {
    position: absolute;
    left: 40px;
    top: 162px;
  }
  .person-name {
    font-size: 24px;
    font-weight: 700;
    color: var(--brand-blue);
    line-height: 1.1;
  }
  .person-title {
    font-size: 14px;
    font-weight: 500;
    margin-bottom: 8px;
  }
  .contact-list {
    list-style: none;
    font-size: 13px;
    font-weight: 500;
    line-height: 1.6;
  }
  .contact-list li {
    display: flex;
    align-items: center;
    gap: 7px;
    white-space: nowrap;
  }
  .contact-list svg {
    width: 13px;
    height: 13px;
    fill: var(--brand-blue);
    flex: none;
  }
  .accent { color: var(--brand-blue); }

  .licensing {
    position: absolute;
    right: 36px;
    top: 158px;
    text-align: right;
    font-size: 13px;
    font-weight: 500;
    line-height: 1.5;
    white-space: nowrap;
  }
  .licensing .address { margin-top: 18px; }

  /* Back */
  .card-back {
    display: flex;
    align-items: center;
    justify-content: center;
  }
  .card-back .brand-name {
    font-size: 64px;
    font-weight: 500;
    letter-spacing: 1px;
    color: var(--brand-blue);
    margin-top: 30px;
  }
</style>
</head>
<body>

  <section class="card card-front" aria-label="Business card front">
    <div class="brand-name">HearthMile</div>
    <div class="divider"></div>

    <div class="person">
      <div class="person-name">Marcus Pell</div>
      <div class="person-title">CEO</div>
      <ul class="contact-list">
        <li>
          <svg viewBox="0 0 24 24" aria-hidden="true"><path d="M6.6 10.8a15.1 15.1 0 0 0 6.6 6.6l2.2-2.2c.3-.3.7-.4 1-.2 1.1.4 2.3.6 3.6.6.6 0 1 .4 1 1V20c0 .6-.4 1-1 1A17 17 0 0 1 3 4c0-.6.4-1 1-1h3.5c.6 0 1 .4 1 1 0 1.3.2 2.5.6 3.6.1.3 0 .7-.2 1z"/></svg>
          732-555-0182
        </li>
        <li>
          <svg viewBox="0 0 24 24" aria-hidden="true"><path d="M2 5h20v14H2z M2 5l10 8 10-8" stroke="#2a2a2a" stroke-width="1.5"/></svg>
          email@hearthmile.example
        </li>
        <li>
          <svg viewBox="0 0 24 24" aria-hidden="true"><circle cx="12" cy="12" r="10"/><path d="M2 12h20M12 2c3 3 3 17 0 20M12 2c-3 3-3 17 0 20" stroke="#2a2a2a" stroke-width="1.4" fill="none"/></svg>
          <span>www.<span class="accent">hearthmile</span>.example</span>
        </li>
      </ul>
    </div>

    <div class="licensing">
      <div><span class="accent">NMLS</span> 61947</div>
      <div><span class="accent">Company NMLS</span> 274615</div>
      <div class="address">48 Birchwell Court, Suite 314<br>Brookvale, NJ 08421</div>
    </div>
  </section>

  <section class="card card-back" aria-label="Business card back">
    <div class="brand-name">HearthMile</div>
  </section>

</body>
</html>
```